Storm Restoration Contractor needs a professional letterhead design

Looking for a professional letterhead design. Not looking for your cheapo MS Word standard ones that are readily available. Dont want it to be cookie cutter look like ones readily available online. We just recently changed our logo and want to freshen up all our documents. Our company handles restoring a property back to a pre-loss condition after a storm damages it. For example, wind, hail, flood, fire losses.

Target Market(s)

Property Owners, Homeowners, Property Owners, Commercial Property Owners, Property Management Companies

Industry/Entity Type

Construction Company

Requirements
Must have
• Professional, Use 1 of 2 logo options
• Storm Restoration, Roofing, Siding, Windows

```html
<!DOCTYPE html>
<html lang="en">
<head>
<meta charset="utf-8">
<title>Stormline Builders — Letterhead &amp; Folder</title>
<link rel="stylesheet" href="https://fonts.googleapis.com/css2?family=Didact+Gothic&family=Lato:wght@400;700&display=swap">
<style>
  :root {
    --bg: #e9edf0;
    --paper: #ffffff;
    --folder: #e1e1e1;
    --brand-blue: #1f7fc8;
    --brand-gray: #58595b;
    --text: #333333;
    --muted: #555555;
    --faint: #d9dadb;
    --watermark: rgba(31,127,200,0.07);
  }
  * { box-sizing: border-box; margin: 0; padding: 0; }
  html, body { width: 1200px; height: 784px; overflow: hidden; }
  body { position: relative; background: var(--bg); font-family: "Didact Gothic", sans-serif; color: var(--text); }

  .letterhead {
    position: absolute; left: 42px; top: 45px; width: 512px; height: 696px;
    background: var(--paper); border-radius: 10px; overflow: hidden;
  }
  .band { position: absolute; left: 0; right: 0; height: 6px; background: var(--brand-gray); }
  .band::before { content: ""; position: absolute; left: 0; top: 0; bottom: 0; background: var(--brand-blue); }
  .band--top { top: 0; }
  .band--top::before { width: 93px; }
  .band--bottom { bottom: 0; }
  .band--bottom::before { width: 148px; }

  .brand { position: absolute; display: flex; align-items: center; gap: 8px; }
  .brand__dot { flex: none; border-radius: 50%; background: var(--brand-blue); }
  .brand__name { font-family: "Didact Gothic", sans-serif; color: var(--brand-gray); line-height: 1.05; text-transform: uppercase; letter-spacing: 1px; }

  .letterhead .brand { left: 48px; top: 52px; }
  .letterhead .brand__dot { width: 38px; height: 38px; }
  .letterhead .brand__name { font-size: 17px; }

  .contact { position: absolute; left: 330px; top: 46px; font-family: "Lato", sans-serif; font-size: 7px; color: var(--muted); list-style: none; }
  .contact li { display: flex; align-items: center; gap: 4px; height: 13.5px; }
  .contact svg { width: 8px; height: 8px; fill: var(--brand-blue); flex: none; }
  .contact .contact__address { font-weight: 700; color: var(--text); }

  .rule { position: absolute; left: 43px; top: 101px; width: 433px; height: 3px; background: var(--brand-gray); }
  .rule::before { content: ""; position: absolute; left: 0; top: 0; width: 215px; height: 100%; background: var(--brand-blue); }
  .website { position: absolute; left: 0; right: 0; top: 110px; text-align: center; font-family: "Lato", sans-serif; font-weight: 700; font-size: 8.5px; letter-spacing: 2.4px; color: var(--brand-blue); }

  .watermark { position: absolute; left: 128px; top: 198px; width: 260px; height: 260px; border-radius: 50%; border: 20px solid var(--watermark); }

  .body-copy { position: absolute; left: 48px; top: 164px; width: 428px; font-size: 10.6px; line-height: 17.9px; text-align: justify; color: var(--text); }
  .body-copy p + p { margin-top: 18px; }

  .footer-mark { position: absolute; left: 48px; top: 604px; font-size: 14px; line-height: 1.05; letter-spacing: 1px; color: var(--faint); text-transform: uppercase; }
  .signature { position: absolute; left: 383px; top: 602px; }
  .signature__name { font-size: 14px; color: var(--text); }
  .signature__title { margin-top: 6px; font-family: "Lato", sans-serif; font-size: 8.5px; color: var(--text); }

  .folder { position: absolute; left: 634px; top: 45px; width: 513px; height: 696px; background: var(--folder); border-radius: 12px; overflow: hidden; }
  .folder__pocket { position: absolute; right: 0; top: 150px; width: 40px; height: 546px; }
  .folder .brand { left: 130px; top: 570px; gap: 14px; }
  .folder .brand__dot { width: 60px; height: 60px; }
  .folder .brand__name { font-size: 28px; }
</style>
</head>
<body>
  <article class="letterhead">
    <div class="band band--top"></div>

    <div class="brand">
      <span class="brand__dot"></span>
      <span class="brand__name">Stormline<br>Builders</span>
    </div>

    <ul class="contact">
      <li><svg viewBox="0 0 10 10"><path d="M2 1l2 2-1 1.3a6 6 0 0 0 2.7 2.7L7 6l2 2-1.2 1.5C4.5 9.3.7 5.5.5 2.2z"/></svg>(800) 555-0142</li>
      <li><svg viewBox="0 0 10 10"><path d="M2.5 0h5v3h-5zM0 3.5h10V8H8v2H2V8H0zM3 6.5v2.5h4V6.5z"/></svg>(800) 555-0178</li>
      <li><svg viewBox="0 0 10 10"><path d="M0 1.5h10v1L5 5.5 0 2.5zM0 3.6l5 3 5-3V8.5H0z"/></svg>hello@stormlinebuilders.com</li>
      <li class="contact__address">480 Harbor Ridge Road, Suite 2, Aldenton, GA 30000</li>
    </ul>

    <div class="rule"></div>
    <p class="website">www.stormlinebuilders.com</p>

    <div class="watermark"></div>

    <div class="body-copy">
      <p>Lorem ipsum dolor sit amet, consectetur adipiscing elit. Donec orci purus, luctus vitae dignissim eu, iaculis sed purus. Vivamus faucibus, ipsum nec aliquet viverra, leo mauris condimentum ligula, sit amet sagittis enim ligula quis arcu. Nam egestas tortor id nisi porttitor mattis. In tortor ante, ultricies in suscipit a, tempus non massa. Vivamus et auctor mi. Fusce vel massa nulla. Phasellus nec eros mauris, et scelerisque orci. Donec malesuada orci vitae nulla accumsan porta a id massa.</p>
      <p>Quisque accumsan iaculis magna sit amet fringilla. Maecenas consequat, magna eget tincidunt semper, odio nibh rutrum mi, id feugiat ante nisi eu risus. Vestibulum nunc orci, rhoncus a placerat in, ultricies in mi. Cras mattis varius eros, vel fringilla nisi suscipit eget. Quisque scelerisque sagittis nulla at porttitor. Mauris a justo et tellus interdum tristique. Sed id augue vitae urna euismod commodo aliquet a quam. Pellentesque arcu velit, cursus et malesuada ut, consequat et diam. Nullam erat sem, rhoncus id ullamcorper vitae, rhoncus et arcu. In ultricies ultricies nulla.</p>
      <p>Kut rutrum nisi iaculis at. Donec eu magna a metus ornare faucibus. Fusce aliquet faucibus ultricies. Morbi semper, est id tincidunt gravida, sem arcu adipiscing lacus, ac bibendum nulla leo eu purus. Quisque nec diam sed risus consectetur a ccumsan quis quis nibh. Vestibulum id purus lorem. Donec eu magna a metus ornare faucibus. Fusce aliquet faucibus ultricies. Morbi semper, est id tincidunt gravida, sem arcu adipiscing lacus, ac bibendum nulla leo eu purus. Quisque nec diam sed risus consectetur a ccumsan quis quis nibh. Vestibulum id purus lorem.</p>
    </div>

    <p class="footer-mark">Stormline<br>Builders</p>

    <div class="signature">
      <p class="signature__name">Dana Whitfield</p>
      <p class="signature__title">Co-Founder &amp; CEO</p>
    </div>

    <div class="band band--bottom"></div>
  </article>

  <article class="folder">
    <svg class="folder__pocket" viewBox="0 0 40 546" preserveAspectRatio="none" aria-hidden="true">
      <path d="M40 0 C20 2 12 8 10 30 L10 546 L40 546 Z" fill="#d8d8d8"/>
      <path d="M40 0 C20 2 12 8 10 30 L10 546" fill="none" stroke="#cfcfcf" stroke-width="1"/>
    </svg>
    <div class="brand">
      <span class="brand__dot"></span>
      <span class="brand__name">Stormline<br>Builders</span>
    </div>
  </article>
</body>
</html>
```